Korvath Supply Website Redesign

Currently korvathsupply.example is focussed on fulfillment and transport from various products in the BBQ segment. However, no we want to update our business activities to Product Development, Brand Development, Online Positioning, Logistics & Aftersales, and Promotional BBQs. We will be a business for Outdoor Leisure Development from A to Z.

Therefore, we need a brand new website. The colours of the current website may be the same. However, i'd like to keep it clean. More white and use blue and green as accent colours. It is a business to business organization so the website should be looking formal and corporate. However we sell fun products so not too formal and corporate.

Pages we need; Home, About, Contact, Our Services (+ page per service) a place to share our news/blogs.

I have added some sort of mock up of an idea. However it needs some finetuning.

Target Market(s)

Businesses

Industry/Entity Type

Corporate/Logistics/Marketing

Coding

Coded - Design and coding required

Colors

Designer to choose colors to be used in the design.

Requirements
Must have
• Show clear distinguishing of the different services we provide (Product Development, Brand Development, Online Positioning, Logistics & Aftersales and Promotional BBQs). Every service should have its own page too. Besides, I would like to have a blog page to share relevant content.
Nice to have
• Show that we are the expert in Outdoor LEisure Development from A to Z
Should not have
• Be too informal. It may be semi-formal

```html
<!DOCTYPE html>
<html lang="en">
<head>
<meta charset="utf-8">
<title>Korvath Supply – Home</title>
<link rel="stylesheet" href="https://fonts.googleapis.com/css2?family=Montserrat:wght@500;600;700;800&family=Roboto:wght@400;500&display=swap">
<style>
:root{
  --board:#2d2d2f;
  --green:#3fae49;
  --teal:#44727e;
  --teal-dark:#3a6571;
  --navy:#10405a;
  --mist:#e6ecee;
  --white:#ffffff;
  --ink:#4b6b75;
}
*{box-sizing:border-box;margin:0;padding:0}
html,body{width:995px;height:1200px;overflow:hidden;background:var(--board)}
.board{position:relative;width:995px;height:1200px;background:var(--board)}
.page{position:absolute;top:60px;width:747px;height:1890px;background:var(--white);transform-origin:0 0;transform:scale(.5715);overflow:hidden;font-family:"Roboto",Arial,sans-serif;color:var(--ink)}
.page--default{left:38.3px}
.page--hover{left:495.5px}
.abs{position:absolute}

/* header */
.site-header{position:absolute;left:0;top:0;width:747px;height:57px;background:var(--white)}
.brand{position:absolute;left:55px;top:12px;display:flex;align-items:center;gap:6px;font-family:"Montserrat",sans-serif;font-weight:800;font-size:30px;color:var(--teal);letter-spacing:-.5px}
.brand-dot{width:20px;height:20px;border-radius:50%;background:var(--green)}
.nav a{position:absolute;top:22px;font-family:"Montserrat",sans-serif;font-weight:700;font-size:8.5px;color:var(--teal);text-decoration:none;letter-spacing:.2px}
.nav a.is-active{color:var(--green)}
.nav-marker{position:absolute;left:246px;top:0;width:40px;height:4px;background:var(--green)}
.nav .tel{color:var(--green)}

/* hero */
.hero-photo{position:absolute;left:0;top:57px;width:747px;height:350px;background:linear-gradient(90deg,#0f3f5a 0%,#15506c 32%,#4c6f86 52%,#8b7f6a 72%,#b49366 100%)}
.hero-title{position:absolute;left:82px;top:128px;font-family:"Montserrat",sans-serif;font-weight:700;font-size:29px;line-height:35.5px;color:var(--white);letter-spacing:.3px}
.hero-curve{position:absolute;left:0;top:330px}

/* section titles */
.section-title{position:absolute;left:0;width:747px;text-align:center;font-family:"Montserrat",sans-serif;font-weight:700;font-size:27px;color:var(--teal)}
.section-title .accent{color:var(--green)}

/* services */
.svc-label{position:absolute;width:130px;margin-left:-65px;text-align:center}
.svc-label h3{font-family:"Montserrat",sans-serif;font-weight:600;font-size:11.5px;line-height:13.5px;color:var(--teal)}
.svc-label h3.is-green{color:var(--green)}
.svc-label p{margin-top:8px;font-size:6.8px;line-height:8.8px;color:var(--ink)}
.svc-circle{position:absolute;width:92px;height:92px;margin:-46px 0 0 -46px;border-radius:50%;display:flex;align-items:center;justify-content:center}
.svc-circle--green{background:var(--green)}
.svc-circle--teal{background:var(--teal)}
.svc-circle.is-hovered{width:100px;height:100px;margin:-50px 0 0 -50px;box-shadow:0 0 0 4px var(--white) inset,0 0 26px 10px rgba(63,174,73,.35);border:0}
.btn{position:absolute;height:20px;padding:0 12px;border-radius:10px;background:var(--green);color:var(--white);font-family:"Montserrat",sans-serif;font-weight:700;font-size:7.5px;line-height:20px;letter-spacing:.3px;text-align:center}

/* difference */
.difference{position:absolute;left:0;top:800px;width:747px;height:370px;background:var(--mist)}
.difference h2{position:absolute;left:82px;top:80px;font-family:"Montserrat",sans-serif;font-weight:700;font-size:27px;line-height:32px;color:var(--teal)}
.difference h2 .accent{color:var(--green)}
.difference p{position:absolute;left:82px;top:155px;width:262px;font-size:8.4px;line-height:13.6px;color:var(--ink)}
.deco-disc{position:absolute;left:528px;top:57px;width:136px;height:136px;border-radius:50%;background:#8fd093}
.photo-disc{position:absolute;left:401px;top:78px;width:240px;height:240px;border-radius:50%;background:linear-gradient(135deg,#c9d4dc 0%,#8ea6bd 40%,#b48a5f 70%,#5c6d7d 100%)}

/* news */
.news-card{position:absolute;top:1297px;width:181px;height:263px;background:var(--white);border-radius:8px;box-shadow:0 2px 10px rgba(60,90,100,.10)}
.news-card.is-hovered{border:3px solid var(--teal)}
.news-photo{position:absolute;left:9px;top:8px;width:162px;height:123px;border-radius:8px}
.news-date{position:absolute;left:15px;top:15px;width:37px;height:37px;border-radius:50%;background:var(--green);color:var(--white);text-align:center;font-family:"Montserrat",sans-serif;font-weight:700;font-size:11px;line-height:10px;padding-top:8px}
.news-date small{display:block;font-size:7px;line-height:9px}
.news-card h3{position:absolute;left:20px;top:155px;width:140px;font-family:"Montserrat",sans-serif;font-weight:600;font-size:12.5px;line-height:13px;color:var(--teal)}
.news-card p{position:absolute;left:20px;top:197px;width:142px;font-size:7.6px;line-height:12.5px;color:var(--ink)}

/* footer */
.site-footer{position:absolute;left:0;top:1600px;width:747px;height:290px;background:var(--teal)}
.footer-brand{position:absolute;left:82px;top:138px;display:flex;align-items:center;gap:8px;font-family:"Montserrat",sans-serif;font-weight:800;font-size:38px;color:var(--white)}
.footer-brand .brand-dot{width:32px;height:32px;background:var(--white)}
.footer-head{position:absolute;top:106px;font-family:"Montserrat",sans-serif;font-weight:600;font-size:14px;color:var(--white);letter-spacing:.3px}
.contact-item{position:absolute;left:335px;display:flex;align-items:flex-start;gap:7px;font-family:"Montserrat",sans-serif;font-size:8.8px;line-height:10px;color:var(--white)}
.contact-item svg{flex:none}
.links{position:absolute;left:595px;top:138px;list-style:none;font-family:"Montserrat",sans-serif;font-size:8.8px;line-height:15px;color:var(--white)}
.copyright{position:absolute;left:0;top:256px;width:747px;text-align:center;font-size:7.5px;color:var(--white)}
</style>
</head>
<body>
<div class="board">

<!-- Default state -->
<div class="page page--default">
  <header class="site-header">
    <div class="brand"><span class="brand-dot"></span>Korvath</div>
    <nav class="nav">
      <span class="nav-marker"></span>
      <a class="is-active" style="left:253px">HOME</a>
      <a style="left:308px">ABOUT</a>
      <a style="left:366px">OUR SERVICES</a>
      <a style="left:459px">CONTACT</a>
      <a style="left:527px">NEWS</a>
      <a class="tel" style="left:590px">TEL: +31 (0)10 555 0147</a>
    </nav>
  </header>

  <div class="hero-photo" role="img" aria-label="Photo: two warehouse staff in hard hats reviewing a clipboard between stocked shelves"></div>
  <h1 class="hero-title">OUTDOOR<br>LEISURE<br>DEVELOPMENT<br>FROM A TO Z</h1>
  <svg class="hero-curve" width="747" height="90" viewBox="0 0 747 90">
    <path d="M0 70 Q373 -4 747 70 L747 90 L0 90Z" fill="#ffffff"/>
    <path d="M55 68 Q373 10 700 62" fill="none" stroke="#3fae49" stroke-width="5"/>
  </svg>

  <h2 class="section-title" style="top:396px"><span class="accent">OUR</span> SERVICES</h2>

  <div class="svc-label" style="left:279px;top:472px"><h3 class="is-green">Brand<br>Development</h3><p>Lorem ipsum dolor sit amet, co nsectetur adipiscing elit, sed do eiusmod tempor incididunt</p></div>
  <div class="svc-label" style="left:466px;top:472px"><h3 class="is-green">Logistics &amp;<br>Aftersales</h3><p>Lorem ipsum dolor sit amet, co nsectetur adipiscing elit, sed do eiusmod tempor incididunt</p></div>

  <div class="svc-circle svc-circle--green" style="left:186px;top:598px">
    <svg width="46" height="46" viewBox="0 0 46 46" fill="none" stroke="#fff" stroke-width="2.4"><circle cx="23" cy="23" r="10" stroke-width="6" stroke-dasharray="4 3"/><circle cx="23" cy="23" r="4"/><path d="M6 18a18 18 0 0 1 28-10M40 28a18 18 0 0 1-28 10"/></svg>
  </div>
  <div class="svc-circle svc-circle--teal" style="left:280px;top:598px">
    <svg width="46" height="46" viewBox="0 0 46 46" fill="none" stroke="#fff" stroke-width="2.2"><path d="M7 17l4-8h24l4 8z"/><path d="M7 17q4 5 8 0q4 5 8 0q4 5 8 0q4 5 8 0"/><rect x="9" y="20" width="28" height="18"/><rect x="13" y="25" width="8" height="13"/><rect x="25" y="25" width="8" height="7"/></svg>
  </div>
  <div class="svc-circle svc-circle--green" style="left:373px;top:598px">
    <svg width="46" height="46" viewBox="0 0 46 46" fill="none" stroke="#fff" stroke-width="2.2"><circle cx="21" cy="21" r="15"/><ellipse cx="21" cy="21" rx="7" ry="15"/><path d="M6 21h30M9 13h24M9 29h24"/><path d="M27 26l12 6-5 2 4 5-3 2-4-5-3 4z" fill="#3fae49"/></svg>
  </div>
  <div class="svc-circle svc-circle--teal" style="left:467px;top:598px">
    <svg width="46" height="46" viewBox="0 0 46 46" fill="none" stroke="#fff" stroke-width="2.2"><path d="M28 18c-4-5-3-11 3-11s7 6 3 11l-3 4z"/><circle cx="31" cy="12" r="2"/><rect x="6" y="22" width="18" height="12"/><path d="M24 26h7l4 5v3h-11"/><circle cx="12" cy="36" r="2.5"/><circle cx="29" cy="36" r="2.5"/><path d="M10 18c-2-3-1-7 2-7s4 4 2 7l-2 2z"/></svg>
  </div>
  <div class="svc-circle svc-circle--green" style="left:560px;top:598px">
    <svg width="46" height="46" viewBox="0 0 46 46" fill="none" stroke="#fff" stroke-width="2.2"><path d="M8 26l4 6 20-6-8-16z"/><path d="M24 10l8 16"/><path d="M12 32l3 7h4l-2-8"/><path d="M34 10l4-3M36 16h5M33 5l1-3"/></svg>
  </div>

  <div class="svc-label" style="left:186px;top:665px"><h3>Product<br>Development</h3><p>Lorem ipsum dolor sit amet, co nsectetur adipiscing elit, sed do eiusmod tempor incididunt</p></div>
  <div class="svc-label" style="left:373px;top:665px"><h3>Online<br>Positioning</h3><p>Lorem ipsum dolor sit amet, co nsectetur adipiscing elit, sed do eiusmod tempor incididunt</p></div>
  <div class="svc-label" style="left:560px;top:665px"><h3>Promotional<br>BBQs</h3><p>Lorem ipsum dolor sit amet, co nsectetur adipiscing elit, sed do eiusmod tempor incididunt</p></div>

  <section class="difference">
    <h2><span class="accent">WE MAKE THE</span><br>DIFFERENCE</h2>
    <p>Lorem ipsum dolor sit amet, consectetur adipiscing elit, sed do eiusmod tempor incididunt ut labore et dolore magna aliqua. Ut enim ad minim veniam, quis nostrud exercitation ullamco laboris nisi ut aliquip ex ea commodo consequat. Duis aute irure dolor in reprehenderit in voluptate velit esse cillum dolore eu fugiat nulla pariatur. Excepteur sint occaecat cupidatat non proident, sunt in culpa qui officia deserunt mollit anim id est laborumLorem ipsum dolor sit amet, consectetur adipiscing elit, sed do eiusmod tempor incididunt ut labore et dolore magna aliqua.</p>
    <div class="deco-disc"></div>
    <div class="photo-disc" role="img" aria-label="Photo: warehouse worker in a hi-vis vest beside a pallet truck and stacked boxes"></div>
  </section>

  <h2 class="section-title" style="top:1238px"><span class="accent">LATEST</span> NEWS</h2>

  <article class="news-card" style="left:82px">
    <div class="news-photo" role="img" aria-label="Photo: cardboard parcels on a sorting conveyor" style="background:linear-gradient(135deg,#c99a63,#7b5a3e 55%,#4d5e70)"></div>
    <div class="news-date">15<small>DEC</small></div>
    <h3>Lorem ipsum dolo sit ametconsectetur</h3>
    <p>Lorem ipsum dolor sit amet, conse ctetur adipiscing elit, sed do eius mod tempor incididun</p>
  </article>
  <article class="news-card" style="left:282px">
    <div class="news-photo" role="img" aria-label="Photo: worker with a tablet checking warehouse shelves" style="background:linear-gradient(135deg,#b8c3cc,#7f93a8 50%,#a88b66)"></div>
    <div class="news-date">15<small>DEC</small></div>
    <h3>Lorem ipsum dolo sit ametconsectetur</h3>
    <p>Lorem ipsum dolor sit amet, conse ctetur adipiscing elit, sed do eius mod tempor incididun</p>
  </article>
  <article class="news-card" style="left:483px">
    <div class="news-photo" role="img" aria-label="Photo: truck on a road by a container port at sunset" style="background:linear-gradient(160deg,#3e4a5c,#c9874a 45%,#8e3b2c 75%,#2f3442)"></div>
    <div class="news-date">15<small>DEC</small></div>
    <h3>Lorem ipsum dolo sit ametconsectetur</h3>
    <p>Lorem ipsum dolor sit amet, conse ctetur adipiscing elit, sed do eius mod tempor incididun</p>
  </article>

  <footer class="site-footer">
    <svg class="abs" style="left:0;top:0" width="747" height="60" viewBox="0 0 747 60"><path d="M0 10 Q373 80 747 10 L747 0 L0 0Z" fill="#ffffff"/><path d="M70 13 Q373 60 720 5" fill="none" stroke="#3fae49" stroke-width="5"/></svg>
    <div class="footer-brand"><span class="brand-dot"></span>Korvath</div>
    <div class="footer-head" style="left:335px">CONTACT</div>
    <div class="contact-item" style="top:140px"><svg width="16" height="16" viewBox="0 0 16 16"><circle cx="8" cy="8" r="8" fill="#3fae49"/><path d="M8 12.5l-3-4a3 3 0 1 1 6 0z" fill="#fff"/></svg><span>Lindqvist Avenue<br>12, 3071 KP Marrowdale</span></div>
    <div class="contact-item" style="top:168px"><svg width="16" height="16" viewBox="0 0 16 16"><circle cx="8" cy="8" r="8" fill="#3fae49"/><path d="M5 4.5l2 2-1 1.2q1 2 2.8 2.8l1.2-1 2 2-1.3 1.3q-4-.5-6-5.5z" fill="#fff"/></svg><span style="padding-top:3px">Marrowdale Office: +31 (0)10 555 0147</span></div>
    <div class="contact-item" style="top:195px"><svg width="16" height="16" viewBox="0 0 16 16"><circle cx="8" cy="8" r="8" fill="#3fae49"/><rect x="4.2" y="5.2" width="7.6" height="5.6" fill="#fff"/><path d="M4.2 5.2l3.8 3 3.8-3" fill="none" stroke="#3fae49" stroke-width=".9"/></svg><span style="padding-top:3px">info@korvathsupply.example</span></div>
    <div class="footer-head" style="left:587px">LINKS</div>
    <ul class="links"><li>Home</li><li>About</li><li>Our Services</li><li>Contact</li><li>News</li></ul>
    <div class="copyright">2021 Copyright © Korvath Supply . All rights reserved.</div>
  </footer>
</div>

<!-- Hover state -->
<div class="page page--hover">
  <header class="site-header">
    <div class="brand"><span class="brand-dot"></span>Korvath</div>
    <nav class="nav">
      <span class="nav-marker"></span>
      <a class="is-active" style="left:253px">HOME</a>
      <a style="left:308px">ABOUT</a>
      <a style="left:366px">OUR SERVICES</a>
      <a style="left:459px">CONTACT</a>
      <a style="left:527px">NEWS</a>
      <a class="tel" style="left:590px">TEL: +31 (0)10 555 0147</a>
    </nav>
  </header>

  <div class="hero-photo" role="img" aria-label="Photo: two warehouse staff in hard hats reviewing a clipboard between stocked shelves"></div>
  <h1 class="hero-title">OUTDOOR<br>LEISURE<br>DEVELOPMENT<br>FROM A TO Z</h1>
  <svg class="hero-curve" width="747" height="90" viewBox="0 0 747 90">
    <path d="M0 70 Q373 -4 747 70 L747 90 L0 90Z" fill="#ffffff"/>
    <path d="M55 68 Q373 10 700 62" fill="none" stroke="#3fae49" stroke-width="5"/>
  </svg>

  <h2 class="section-title" style="top:396px"><span class="accent">OUR</span> SERVICES</h2>

  <div class="svc-label" style="left:279px;top:472px"><h3 class="is-green">Brand<br>Development</h3><p>Lorem ipsum dolor sit amet, co nsectetur adipiscing elit, sed do eiusmod tempor incididunt</p></div>
  <div class="svc-label" style="left:466px;top:472px"><h3 class="is-green">Logistics &amp;<br>Aftersales</h3><p>Lorem ipsum dolor sit amet, co nsectetur adipiscing elit, sed do eiusmod tempor incididunt</p></div>

  <div class="svc-circle svc-circle--green" style="left:186px;top:598px">
    <svg width="46" height="46" viewBox="0 0 46 46" fill="none" stroke="#fff" stroke-width="2.4"><circle cx="23" cy="23" r="10" stroke-width="6" stroke-dasharray="4 3"/><circle cx="23" cy="23" r="4"/><path d="M6 18a18 18 0 0 1 28-10M40 28a18 18 0 0 1-28 10"/></svg>
  </div>
  <div class="svc-circle svc-circle--teal" style="left:280px;top:598px">
    <svg width="46" height="46" viewBox="0 0 46 46" fill="none" stroke="#fff" stroke-width="2.2"><path d="M7 17l4-8h24l4 8z"/><path d="M7 17q4 5 8 0q4 5 8 0q4 5 8 0q4 5 8 0"/><rect x="9" y="20" width="28" height="18"/><rect x="13" y="25" width="8" height="13"/><rect x="25" y="25" width="8" height="7"/></svg>
  </div>
  <div class="svc-circle svc-circle--teal" style="left:467px;top:598px">
    <svg width="46" height="46" viewBox="0 0 46 46" fill="none" stroke="#fff" stroke-width="2.2"><path d="M28 18c-4-5-3-11 3-11s7 6 3 11l-3 4z"/><circle cx="31" cy="12" r="2"/><rect x="6" y="22" width="18" height="12"/><path d="M24 26h7l4 5v3h-11"/><circle cx="12" cy="36" r="2.5"/><circle cx="29" cy="36" r="2.5"/><path d="M10 18c-2-3-1-7 2-7s4 4 2 7l-2 2z"/></svg>
  </div>
  <div class="svc-circle svc-circle--green is-hovered" style="left:373px;top:598px">
    <svg width="46" height="46" viewBox="0 0 46 46" fill="none" stroke="#fff" stroke-width="2.2"><circle cx="21" cy="21" r="15"/><ellipse cx="21" cy="21" rx="7" ry="15"/><path d="M6 21h30M9 13h24M9 29h24"/><path d="M27 26l12 6-5 2 4 5-3 2-4-5-3 4z" fill="#3fae49"/></svg>
  </div>
  <div class="svc-circle svc-circle--green" style="left:560px;top:598px">
    <svg width="46" height="46" viewBox="0 0 46 46" fill="none" stroke="#fff" stroke-width="2.2"><path d="M8 26l4 6 20-6-8-16z"/><path d="M24 10l8 16"/><path d="M12 32l3 7h4l-2-8"/><path d="M34 10l4-3M36 16h5M33 5l1-3"/></svg>
  </div>
  <svg class="abs" style="left:393px;top:616px" width="20" height="26" viewBox="0 0 20 26"><path d="M6 2q2-1.5 3 0v9l1-1q2-1 3 .5l1-.5q2-1 3 1l.5-.3q2 0 2 2v6q0 4-4 6h-6q-3-1-5-5l-3-5q0-2 2-1.5l2 2V3z" fill="#fff" stroke="#1f2b33" stroke-width="1.1"/></svg>

  <div class="svc-label" style="left:186px;top:665px"><h3>Product<br>Development</h3><p>Lorem ipsum dolor sit amet, co nsectetur adipiscing elit, sed do eiusmod tempor incididunt</p></div>
  <div class="svc-label" style="left:373px;top:665px"><h3>Online<br>Positioning</h3><p>Lorem ipsum dolor sit amet, co nsectetur adipiscing elit, sed do eiusmod tempor incididunt</p></div>
  <div class="svc-label" style="left:560px;top:665px"><h3>Promotional<br>BBQs</h3><p>Lorem ipsum dolor sit amet, co nsectetur adipiscing elit, sed do eiusmod tempor incididunt</p></div>
  <div class="btn" style="left:333px;top:743px;width:80px">READ MORE</div>

  <section class="difference">
    <h2><span class="accent">WE MAKE THE</span><br>DIFFERENCE</h2>
    <p>Lorem ipsum dolor sit amet, consectetur adipiscing elit, sed do eiusmod tempor incididunt ut labore et dolore magna aliqua. Ut enim ad minim veniam, quis nostrud exercitation ullamco laboris nisi ut aliquip ex ea commodo consequat. Duis aute irure dolor in reprehenderit in voluptate velit esse cillum dolore eu fugiat nulla pariatur. Excepteur sint occaecat cupidatat non proident, sunt in culpa qui officia deserunt mollit anim id est laborumLorem ipsum dolor sit amet, consectetur adipiscing elit, sed do eiusmod tempor incididunt ut labore et dolore magna aliqua.</p>
    <div class="deco-disc"></div>
    <div class="photo-disc" role="img" aria-label="Photo: warehouse worker in a hi-vis vest beside a pallet truck and stacked boxes"></div>
  </section>

  <h2 class="section-title" style="top:1238px"><span class="accent">LATEST</span> NEWS</h2>

  <article class="news-card" style="left:82px">
    <div class="news-photo" role="img" aria-label="Photo: cardboard parcels on a sorting conveyor" style="background:linear-gradient(135deg,#c99a63,#7b5a3e 55%,#4d5e70)"></div>
    <div class="news-date">15<small>DEC</small></div>
    <h3>Lorem ipsum dolo sit ametconsectetur</h3>
    <p>Lorem ipsum dolor sit amet, conse ctetur adipiscing elit, sed do eius mod tempor incididun</p>
  </article>
  <article class="news-card" style="left:282px">
    <div class="news-photo" role="img" aria-label="Photo: worker with a tablet checking warehouse shelves" style="background:linear-gradient(135deg,#b8c3cc,#7f93a8 50%,#a88b66)"></div>
    <div class="news-date">15<small>DEC</small></div>
    <h3>Lorem ipsum dolo sit ametconsectetur</h3>
    <p>Lorem ipsum dolor sit amet, conse ctetur adipiscing elit, sed do eius mod tempor incididun</p>
  </article>
  <article class="news-card is-hovered" style="left:483px">
    <div class="news-photo" role="img" aria-label="Photo: truck on a road by a container port at sunset" style="background:linear-gradient(160deg,#3e4a5c,#c9874a 45%,#8e3b2c 75%,#2f3442)"></div>
    <div class="news-date">15<small>DEC</small></div>
    <h3>Lorem ipsum dolo sit ametconsectetur</h3>
    <p>Lorem ipsum dolor sit amet, conse ctetur adipiscing elit, sed do eius mod tempor incididun</p>
  </article>
  <div class="btn" style="left:506px;top:1547px;width:78px">READ MORE</div>
  <svg class="abs" style="left:628px;top:1526px" width="20" height="26" viewBox="0 0 20 26"><path d="M6 2q2-1.5 3 0v9l1-1q2-1 3 .5l1-.5q2-1 3 1l.5-.3q2 0 2 2v6q0 4-4 6h-6q-3-1-5-5l-3-5q0-2 2-1.5l2 2V3z" fill="#fff" stroke="#1f2b33" stroke-width="1.1"/></svg>

  <footer class="site-footer">
    <svg class="abs" style="left:0;top:0" width="747" height="60" viewBox="0 0 747 60"><path d="M0 10 Q373 80 747 10 L747 0 L0 0Z" fill="#ffffff"/><path d="M70 13 Q373 60 720 5" fill="none" stroke="#3fae49" stroke-width="5"/></svg>
    <div class="footer-brand"><span class="brand-dot"></span>Korvath</div>
    <div class="footer-head" style="left:335px">CONTACT</div>
    <div class="contact-item" style="top:140px"><svg width="16" height="16" viewBox="0 0 16 16"><circle cx="8" cy="8" r="8" fill="#3fae49"/><path d="M8 12.5l-3-4a3 3 0 1 1 6 0z" fill="#fff"/></svg><span>Lindqvist Avenue<br>12, 3071 KP Marrowdale</span></div>
    <div class="contact-item" style="top:168px"><svg width="16" height="16" viewBox="0 0 16 16"><circle cx="8" cy="8" r="8" fill="#3fae49"/><path d="M5 4.5l2 2-1 1.2q1 2 2.8 2.8l1.2-1 2 2-1.3 1.3q-4-.5-6-5.5z" fill="#fff"/></svg><span style="padding-top:3px">Marrowdale Office: +31 (0)10 555 0147</span></div>
    <div class="contact-item" style="top:195px"><svg width="16" height="16" viewBox="0 0 16 16"><circle cx="8" cy="8" r="8" fill="#3fae49"/><rect x="4.2" y="5.2" width="7.6" height="5.6" fill="#fff"/><path d="M4.2 5.2l3.8 3 3.8-3" fill="none" stroke="#3fae49" stroke-width=".9"/></svg><span style="padding-top:3px">info@korvathsupply.example</span></div>
    <div class="footer-head" style="left:587px">LINKS</div>
    <ul class="links"><li>Home</li><li>About</li><li>Our Services</li><li>Contact</li><li>News</li></ul>
    <div class="copyright">2021 Copyright © Korvath Supply . All rights reserved.</div>
  </footer>
</div>

</div>
</body>
</html>
```